1876 Basins & Spouts Business Card

I'm wanting to get a business card designed. Our business is 1876 Basins & Spouts
Details for the card:

1876 Basins & Spouts
Name: Harold Vesk
Email: harold@1876basinsandspouts.com.au
Website: www.1876basinsandspouts.com.au
Mobile: 0438 260 947
Phone: 02 7481 3926

Font of Basins & Spouts is called Snell Roundhand. Not sue what font logo text is.

I'm thinking two sided but it doesn't have to be.

```html
<!DOCTYPE html>
<html lang="en">
<head>
<meta charset="utf-8">
<title>1876 Basins &amp; Spouts Business Card</title>
<link rel="stylesheet" href="https://fonts.googleapis.com/css2?family=Cormorant+Garamond:wght@500&family=Open+Sans:wght@400;700&family=Pinyon+Script&display=swap">
<style>
  :root {
    --backdrop: #2b2b2c;
    --card: #1d1d1e;
    --card-pattern: #262627;
    --ink: #f2f2f2;
    --ink-soft: #b9b9b9;
    --rule: #6a6a6a;
  }
  * { box-sizing: border-box; margin: 0; padding: 0; }
  html, body { width: 1200px; height: 1108px; overflow: hidden; }
  body {
    background: var(--backdrop);
    display: flex;
    justify-content: center;
    align-items: center;
    gap: 70px;
  }
  .card {
    position: relative;
    width: 400px;
    height: 650px;
    background: var(--card);
    border-radius: 22px;
    overflow: hidden;
  }
  .brand {
    position: absolute;
    left: 34px;
    top: 56px;
    display: flex;
    align-items: center;
    gap: 14px;
  }
  .brand-mark {
    width: 58px;
    height: 58px;
    border: 2px solid var(--ink-soft);
    border-radius: 50%;
    flex: none;
  }
  .brand-name {
    font-family: "Cormorant Garamond", serif;
    font-weight: 500;
    font-size: 30px;
    color: var(--ink);
    line-height: 1;
    white-space: nowrap;
  }
  .tagline {
    position: absolute;
    left: 34px;
    top: 128px;
    font-family: "Open Sans", sans-serif;
    font-size: 11px;
    color: var(--ink-soft);
    letter-spacing: 0.2px;
    white-space: nowrap;
  }
  .contact {
    position: absolute;
    left: 0;
    right: 0;
    top: 395px;
    text-align: center;
    color: var(--ink-soft);
    font-family: "Open Sans", sans-serif;
  }
  .holder {
    font-family: "Pinyon Script", cursive;
    font-size: 38px;
    color: var(--ink);
    line-height: 1.2;
  }
  .divider {
    width: 200px;
    height: 1px;
    background: var(--rule);
    margin: 6px auto 14px;
  }
  .contact-line {
    font-size: 17px;
    line-height: 1.35;
  }
  .contact-line b { font-weight: 700; color: var(--ink); }
  .web-lines { font-size: 15.5px; line-height: 1.4; }
  .pattern-field {
    position: absolute;
    inset: 0 0 150px 0;
    background: linear-gradient(180deg, var(--card-pattern), var(--card));
  }
  .back-name {
    position: absolute;
    left: 0;
    right: 0;
    bottom: 70px;
    text-align: center;
    font-family: "Cormorant Garamond", serif;
    font-weight: 500;
    font-size: 46px;
    color: var(--ink);
    white-space: nowrap;
  }
</style>
</head>
<body>
  <section class="card card-front">
    <div class="brand">
      <span class="brand-mark"></span>
      <span class="brand-name">1876 Basins &amp; Spouts</span>
    </div>
    <p class="tagline">Pairing enduring elegance with everyday usefulness</p>
    <div class="contact">
      <p class="holder">Harold Vesk</p>
      <div class="divider"></div>
      <p class="contact-line"><b>P:</b> 0438 260 947</p>
      <p class="contact-line"><b>M:</b> 02 7481 3926</p>
      <div class="web-lines">
        <p>harold@1876basinsandspouts.com.au</p>
        <p>www.1876basinsandspouts.com.au</p>
      </div>
    </div>
  </section>
  <section class="card card-back">
    <div class="pattern-field" role="img" aria-label="Faint repeating pattern of the brand emblem"></div>
    <p class="back-name">Basins &amp; Spouts</p>
  </section>
</body>
</html>
```